I need a business card design for a new dance business. I offer classical Indian dance tuition and also professional performances. I want to offer the community a variety of Indian dance experiences which include: group class and private tuition, school and preschool educational courses and workshops. dance theatre performances, community function workshops and performances, Kids Bollywood parties, wedding & conference performances, mouth percussion classes, Indian mythology/ dance costume and make up workshops.
The final design should communicate a feeling and impression of the vibrance and energy of Indian dance.
Updates
Hi Everyone,
Project Deadline Extended
Reason: I would like to refine a few changes to the details of this lovely design and we have run out of time!
Project Deadline Extended
Reason: Still waiting to hear back form designer re two possible changes to the card design. Tomorrow is the deadline and I have sent several messages but with no response. I need to see this through before selecting this lovely design.
Thank you.
Tara
Industry/Entity Type
Preschool
Requirements
Must have
- The front of the business card should have the photo of me (my face and torso), surrounded entirely by a border of bright magenta (to match the magenta of my lipstick - it is the same as the magenta on my skirt in the second photo). Within the top border I want (perhaps yellow-gold) writing to say "Tara Holloway - Artistic Director" and within the bottom border it should read "Saffron Lantern Indian Dance." If you turn the card on its side the left border should have my telephone number: 0417 862 493 and the right-hand border should read: saffronlanternindiandance@quillmail.example
The reverse of the card should be the orange of the dance costume
and I'd like the picture of my feet and legs to be on the right side of the back of the card as a side border. Centre-aligned on the orange background it should read (perhaps in dark magenta):
Indian dance classes + private tuition
School + preschool educational courses and workshops
Dance theatre performances
Community function workshops and performances
Children's Bollywood parties
Wedding + conference performances
Mouth percussion classes
Indian mythology and dance demonstration workshops
Dance costume and make-up workshops
Nice to have
- A lovely artistic but easy-to-read font would be nice.

```html
<!DOCTYPE html>
<html lang="en">
<head>
<meta charset="utf-8">
<title>Saffron Lantern Indian Dance – Business Card</title>
<link rel="stylesheet" href="https://fonts.googleapis.com/css2?family=Arimo:wght@400;700&family=Kaushan+Script&display=swap">
<style>
  :root {
    --page: #ffffff;
    --orange-light: #f6a623;
    --orange: #f28a22;
    --orange-deep: #ee6f24;
    --brown-dark: #2a1410;
    --brown-text: #5a1e0c;
    --magenta: #9b1d5a;
    --magenta-deep: #6e1230;
    --gold: #d9902e;
    --white: #ffffff;
  }
  * { box-sizing: border-box; margin: 0; padding: 0; }
  html, body {
    width: 1200px; height: 900px; overflow: hidden;
    background: var(--page);
    font-family: "Arimo", Helvetica, Arial, sans-serif;
  }
  .canvas { position: relative; width: 1200px; height: 900px; }

  .card {
    position: absolute; top: 172px;
    width: 310px; height: 558px;
    overflow: hidden;
    box-shadow: 2px 3px 5px rgba(0,0,0,0.25);
  }
  .card--front { left: 280px; background: var(--white); }
  .card--back {
    left: 613px;
    background: linear-gradient(100deg, var(--orange-light) 0%, var(--orange) 45%, var(--orange-deep) 100%);
  }

  /* Front */
  .front__photo {
    position: absolute; left: 10px; top: 0; width: 290px; height: 375px;
    background: linear-gradient(160deg, var(--gold) 0%, var(--magenta) 35%, var(--magenta-deep) 60%, var(--orange) 100%);
    border-radius: 0 0 40px 0;
  }
  .front__panel {
    position: absolute; left: 0; top: 375px; width: 310px; height: 183px;
    background: linear-gradient(100deg, var(--orange-deep) 0%, var(--orange-light) 50%, var(--orange) 100%);
    text-align: center;
  }
  .brand__name {
    margin-top: 12px;
    font-size: 27px; font-weight: 400; color: var(--brown-text);
    line-height: 1.15; letter-spacing: -0.2px;
  }
  .brand__sub {
    font-size: 24px; font-weight: 400; color: var(--brown-text);
    line-height: 1.1;
  }
  .front__dancer {
    position: absolute; left: 0; right: 0; top: 105px;
    font-family: "Kaushan Script", "Brush Script MT", cursive;
    font-size: 40px; color: var(--white); white-space: nowrap;
    text-shadow: 1px 1px 2px rgba(0,0,0,0.3);
  }
  .front__credential {
    position: absolute; left: 0; right: 0; bottom: 8px;
    font-size: 12.5px; color: var(--brown-text);
  }

  /* Back */
  .back__header {
    position: absolute; left: 0; top: 0; width: 310px; height: 73px;
    background: var(--brown-dark);
    color: var(--white); text-align: right; padding: 12px 10px 0 0;
  }
  .contact__phone { font-size: 19px; line-height: 1.2; }
  .contact__email { font-size: 14.5px; line-height: 1.3; margin-top: 1px; }

  .back__portrait {
    position: absolute; left: 0; top: 55px; width: 170px; height: 503px;
    background: linear-gradient(180deg, var(--orange-light) 0%, var(--magenta) 45%, var(--magenta-deep) 80%, var(--gold) 100%);
    border-radius: 0 70px 0 0;
    opacity: 0.9;
  }
  .services {
    position: absolute; right: 10px; top: 130px; width: 200px;
    list-style: none; text-align: right;
    color: var(--white); font-size: 12.5px; line-height: 17.5px;
  }
  .services li { margin-bottom: 17.5px; }
</style>
</head>
<body>
<div class="canvas">

  <section class="card card--front">
    <div class="front__photo" role="img" aria-label="Photograph of a dancer's leg and foot in a magenta and gold silk costume with ankle bells"></div>
    <div class="front__panel">
      <h1 class="brand__name">SAFFRON LANTERN</h1>
      <p class="brand__sub">INDIAN DANCE</p>
      <p class="front__dancer">Tara Holloway</p>
      <p class="front__credential">Graduate of Kuchipudi classical Indian dance</p>
    </div>
  </section>

  <section class="card card--back">
    <div class="back__portrait" role="img" aria-label="Photograph of the dancer in classical costume with jewellery and flowers in her hair"></div>
    <header class="back__header">
      <p class="contact__phone">0417 862 493</p>
      <p class="contact__email">saffronlanternindiandance@quillmail.example</p>
    </header>
    <ul class="services">
      <li>Indian dance classes<br>+ private tuition</li>
      <li>School + preschool educational<br>courses and workshops</li>
      <li>Dance theatre performances</li>
      <li>Community function workshops<br>and performances</li>
      <li>Children's parties</li>
      <li>Wedding + conference<br>performances</li>
      <li>Mouth percussion classes</li>
      <li>Indian mythology and dance<br>demonstration workshops</li>
    </ul>
  </section>

</div>
</body>
</html>
```